Company brochure for our unique consulting business

We are a small consulting business offering a unique set of services to our clients.. In simple terms we are a business improvement consultancy helping our clients get the best out of their businesses. We work with clients across multiple sectors and deliver a variety of services. We want to put together a brochure to cover these main themes:1. Who we are2. What we do3. The type of people we employ4. The sectors we work inWhile the brochure needs to have a certain corporate feel to it, we don't want it to be "boring" or "stiff". We would like it to have a slightly "friendly" or "informal" feel to it, to reflect the type of organisation we are.We have a company website http://brevalconsultingpartners.net , however we do not want to directly replicate the content or feel as we recognise it needs updating.We would like the brochure to be A4 portrait format. We anticipate requiring 12 sides (including covers) but we are happy to be guided on this based on the content we have provided.The attached ppt file gives the detail of the content to be included and also shows the proposed pagination. For the front cover we would like to try 2 versions, one with the BCP logo and one with the Breval Consulting Partners logo (a file of both is attached)One of the most important pages will be the "Our Services" page. We would like this to cover the centre fold. In the ppt file we have shown an example layout, but this is where we need most help - we are clearly not graphic designers! This page will be the most used page in sales meetings etc.Also attached is the following:1. file for our BrevalConsulting Partners company logo.2. File for our BCP company logo3. Files for Derek's signatures (for under photos) - Owen's to follow4. Photo of Derek & Owen (person in purple shirt to be cropped out)Thank you and really excited to see what everyone comes back with.Derek & Owen

Target Market(s)

Very broad - Manufacturing, Healthcare, Hospitality

Industry/Entity Type

Management Consulting

Font styles to use
Other font styles liked:
• We use Swiss721, but happy to be guided by designer

Colors
3276b5
85abd2
0355a3
333333
5c5c5c
9d9d9d
d9d9d9

Requirements
Must have
• Corporate feel
Nice to have
• Slightly friendly feel
• Our standard "blue" is (CORRECTION) - R55 G96 B146 #376092 and our standard grey is R197 G178, B179 - #B3B2B2, which we would like to keep, but other colours we are happy to be guided on. Brand guidelines attached.

```html
<!DOCTYPE html>
<html lang="en">
<head>
<meta charset="utf-8">
<title>Breval Consulting Partners – Brochure Cover</title>
<link rel="stylesheet" href="https://fonts.googleapis.com/css2?family=Lato:wght@400;700&display=swap">
<style>
  :root {
    --page-bg: #e9e9e9;
    --paper: #ffffff;
    --brand-blue: #376092;
    --accent-green: #5d9a35;
    --accent-gold: #c29a3e;
    --headline-red: #8a1f23;
    --url-red: #a8575a;
    --logo-ink: #1d1d1f;
    --photo-warm: #c9a58a;
    --photo-cool: #d8dde3;
  }
  * { box-sizing: border-box; margin: 0; padding: 0; }
  html, body {
    width: 1200px;
    height: 960px;
    overflow: hidden;
    background: var(--page-bg);
    font-family: "Lato", Arial, sans-serif;
  }
  .canvas {
    width: 1200px;
    height: 960px;
    display: flex;
    align-items: center;
    justify-content: center;
  }
  .cover {
    position: relative;
    width: 590px;
    height: 834px;
    background: var(--paper);
    box-shadow: 0 10px 30px rgba(0,0,0,0.12);
    overflow: hidden;
  }
  .cover__band {
    position: absolute;
    left: 0; top: 0;
    width: 100%;
    height: 352px;
    background: var(--brand-blue);
  }
  .cover__tagline {
    position: absolute;
    left: 48px;
    top: 92px;
    color: #ffffff;
    font-size: 13px;
    letter-spacing: 0.04em;
    text-transform: uppercase;
  }
  .cover__visual {
    position: absolute;
    left: 48px;
    top: 132px;
    width: 360px;
    height: 440px;
  }
  .cover__logo {
    position: absolute;
    right: 40px;
    top: 470px;
    width: 200px;
    text-align: right;
    color: var(--logo-ink);
    font-weight: 700;
    font-size: 24px;
    line-height: 1.1;
  }
  .cover__headline {
    position: absolute;
    left: 150px;
    top: 668px;
    color: var(--headline-red);
    font-size: 21px;
    line-height: 1.15;
    font-weight: 400;
  }
  .cover__url {
    position: absolute;
    left: 150px;
    top: 730px;
    color: var(--url-red);
    font-size: 11px;
    letter-spacing: 0.02em;
  }
</style>
</head>
<body>
<main class="canvas">
  <article class="cover">
    <div class="cover__band"></div>
    <p class="cover__tagline">Better people, better business</p>

    <svg class="cover__visual" viewBox="0 0 360 440" aria-hidden="false">
      <defs>
        <linearGradient id="photoTone" x1="0" y1="0" x2="1" y2="1">
          <stop offset="0" stop-color="var(--photo-warm)"/>
          <stop offset="1" stop-color="var(--photo-cool)"/>
        </linearGradient>
      </defs>
      <polygon role="img" aria-label="Photo of a smiling team gathered around a laptop in a bright office"
               points="0,0 290,0 290,40 340,300 325,440 0,440" fill="url(#photoTone)"/>
      <polygon class="accent-gold" points="290,40 340,40 360,300 325,300" fill="var(--accent-gold)"/>
      <polygon class="accent-green" points="290,0 340,0 340,40 290,40" fill="var(--accent-green)"/>
    </svg>

    <div class="cover__logo">Breval Consulting Partners</div>

    <h1 class="cover__headline">business improvement<br>by brevalconsultingpartners</h1>
    <p class="cover__url">brevalconsultingpartners.net</p>
  </article>
</main>
</body>
</html>
```